Website Design for R W Builders: Showcasing Excellence in General Contracting

R W Builders, a leading general contractor based in California, is seeking a professional and engaging website design to effectively showcase our expertise, services, and commitment to excellence. The website will serve as a digital platform to represent our brand identity, highlight our portfolio, and attract potential clients in various sectors.

Key Objectives:

Reflect Company Identity: The website should accurately reflect the identity and values of R W Builders, including our dedication to quality, professionalism, and client satisfaction.
Showcase Services: Highlight our wide range of general contracting services, including but not limited to construction management, design-build, renovation, and commercial construction.
Portfolio Display: Display an extensive portfolio of past projects completed by R W Builders, showcasing our capabilities, craftsmanship, and successful outcomes.
Client Testimonials: Incorporate client testimonials and case studies to demonstrate our track record of delivering projects on time, within budget, and to the highest standards.
Contact Information: Ensure easy access to contact information, including phone number, email, and physical address, to facilitate communication with potential clients.
Responsive Design: Develop a responsive website design optimized for various devices and screen sizes, ensuring a seamless user experience across desktops, laptops, tablets, and smartphones.
Search Engine Optimization (SEO): Implement SEO best practices to enhance the visibility of the website on search engines, increasing organic traffic and generating leads.
User-Friendly Navigation: Create an intuitive and user-friendly navigation structure that enables visitors to easily find the information they need, such as services, portfolio, testimonials, and contact details.
Visual Appeal: Utilize visually appealing graphics, images, and layout designs to capture the attention of visitors and leave a lasting impression of professionalism and quality.
Compliance and Security: Ensure compliance with industry standards and regulations, as well as implementing necessary security measures to protect user data and privacy.

```html
<!DOCTYPE html>
<html lang="en">
<head>
<meta charset="utf-8">
<title>R W Builders</title>
<link href="https://fonts.googleapis.com/css2?family=Roboto:wght@400;500;700&display=swap" rel="stylesheet">
<style>
:root{--blue:#0aa5e8;--light:#dff2fb;--dark:#1c1c1c;--text:#111;--muted:#555;--white:#fff}
*{box-sizing:border-box;margin:0;padding:0}
html,body{width:1200px;height:3699px;overflow:hidden}
body{font-family:Roboto,sans-serif;color:var(--text);background:var(--white);position:relative}
.abs{position:absolute}
.topbar{left:300px;top:0;width:900px;height:64px;background:var(--blue);border-bottom-left-radius:40px;display:flex;align-items:center;padding-left:30px;gap:0}
.contact{display:flex;align-items:center;gap:14px;color:var(--white);font-size:14px;line-height:1.4}
.contact b{display:block;font-size:12px;font-weight:500}
.ic{width:36px;height:36px;border-radius:50%;background:#111;display:flex;align-items:center;justify-content:center;flex:none}
.ic.blue{background:var(--blue)}
.logo{left:100px;top:52px;width:160px;text-align:center;font-weight:700;font-size:26px;color:#000}
.nav{left:332px;top:108px;display:flex;gap:53px;font-size:15px;color:#222}
.btn{display:inline-flex;align-items:center;justify-content:center;background:var(--blue);color:var(--white);border-radius:22px;font-size:14px;font-weight:500}
.start{left:916px;top:97px;width:172px;height:42px}
.hero{left:0;top:171px;width:1200px;height:600px;border-radius:0 0 60px 60px;background:linear-gradient(180deg,#4a4f55 0%,#5a5d5c 45%,#6e5a44 75%,#5b3f28 100%);overflow:hidden}
.hero h1{position:absolute;top:180px;width:100%;text-align:center;color:var(--white);font-size:72px;font-weight:700}
.hero p{position:absolute;top:280px;width:100%;text-align:center;color:var(--white);font-size:20px;line-height:30px;font-weight:500}
.hero .btn{position:absolute;left:508px;top:368px;width:172px;height:42px}
.sec-title{width:1200px;text-align:center;font-size:48px;font-weight:700}
.tab{top:937px;width:320px;height:66px;border-radius:33px;font-size:25px;font-weight:500;display:flex;align-items:center;justify-content:center}
.tab.on{left:256px;background:var(--blue);color:var(--white)}
.tab.off{left:625px;border:3px solid var(--blue);color:var(--blue)}
.card{width:300px;text-align:center}
.card .ph{height:240px}
.card h3{font-size:20px;font-weight:500;margin-top:24px;line-height:26px}
.card p{font-size:15px;line-height:26px;color:var(--muted);margin:14px auto 0;width:270px}
.card .btn{width:154px;height:42px;margin-top:18px;font-size:15px}
.arrow{width:28px;height:28px}
.testi{left:0;top:1577px;width:1200px;height:600px;background:var(--light);border-radius:60px 60px 0 0}
.av{width:82px;height:82px;border-radius:50%;border:3px solid var(--light)}
.tname{top:1898px;width:1200px;text-align:center;color:var(--blue);font-size:20px;font-weight:500}
.trole{top:1928px;width:1200px;text-align:center;font-size:13px}
.tquote{left:210px;top:1956px;width:780px;text-align:center;font-size:15px;line-height:26px;color:var(--muted)}
.stars{top:2072px;width:1200px;text-align:center;color:var(--blue);font-size:16px;letter-spacing:1px}
.exp-text{left:210px;top:2996px;width:780px;text-align:center;font-size:15px;line-height:26px;color:var(--muted)}
.feat{top:3095px;width:200px;text-align:center;font-size:20px;line-height:30px;color:#222}
.feat svg{display:block;margin:0 auto 14px;height:72px}
.footer{left:0;top:3328px;width:1200px;height:371px;background:var(--dark);border-radius:60px 60px 0 0}
.flogo{left:0;top:3440px;width:1200px;text-align:center;color:var(--white);font-weight:700;font-size:28px}
.fcontacts{left:220px;top:3578px;display:flex;gap:50px}
.copy{top:3662px;width:1200px;text-align:center;color:var(--white);font-size:13px}
</style>
</head>
<body>

<header>
  <div class="abs logo">R W Builders</div>
  <div class="abs topbar">
    <div class="contact" style="width:212px"><span class="ic"><svg width="16" height="16" viewBox="0 0 24 24"><path fill="#fff" d="M6.6 10.8a15 15 0 0 0 6.6 6.6l2.2-2.2c.3-.3.7-.4 1-.2 1.1.4 2.3.6 3.6.6.6 0 1 .4 1 1V20c0 .6-.4 1-1 1A17 17 0 0 1 3 4c0-.6.4-1 1-1h3.5c.6 0 1 .4 1 1 0 1.3.2 2.5.6 3.6.1.3 0 .7-.2 1z"/></svg></span><span><b>Call</b>(555) 410-2286</span></div>
    <div class="contact" style="width:248px"><span class="ic"><svg width="16" height="16" viewBox="0 0 24 24"><rect x="2" y="5" width="20" height="14" rx="2" fill="#fff"/><path d="M2 6l10 7 10-7" stroke="#111" stroke-width="2" fill="none"/></svg></span><span><b>Email</b>hello@rwbuilders.biz</span></div>
    <div class="contact"><span class="ic"><svg width="16" height="16" viewBox="0 0 24 24"><path fill="#fff" d="M12 2a7 7 0 0 0-7 7c0 5 7 13 7 13s7-8 7-13a7 7 0 0 0-7-7zm0 9.5A2.5 2.5 0 1 1 12 6.5a2.5 2.5 0 0 1 0 5z"/></svg></span><span><b>Location</b>P.O. Box 2480 Arroyo Vista, CA 93401</span></div>
  </div>
  <nav class="abs nav"><span>Home</span><span>Services</span><span>Portfolio</span><span>Testimonials</span><span>Contact</span></nav>
  <span class="abs btn start">Get Started</span>
</header>

<section class="abs hero" role="img" aria-label="Excavator working on a dirt construction site under a cloudy sky">
  <h1>Welcome to R W Builders</h1>
  <p>Since 2013, R W Builders has been a thriving 8(a) certified General Contractor,<br>consistently delivering successful projects to a diverse array of clients.</p>
  <span class="btn">Contact Us</span>
</section>

<h2 class="abs sec-title" style="top:848px">Our Services</h2>
<div class="abs tab on">Specialized Services</div>
<div class="abs tab off">General Contracting</div>

<svg class="abs arrow" style="left:61px;top:1175px" viewBox="0 0 28 28"><circle cx="14" cy="14" r="14" fill="#0aa5e8"/><path d="M20 14H9M13 9l-5 5 5 5" stroke="#fff" stroke-width="3" fill="none" stroke-linecap="round" stroke-linejoin="round"/></svg>
<svg class="abs arrow" style="left:1109px;top:1175px" viewBox="0 0 28 28"><circle cx="14" cy="14" r="14" fill="#0aa5e8"/><path d="M8 14h11M15 9l5 5-5 5" stroke="#fff" stroke-width="3" fill="none" stroke-linecap="round" stroke-linejoin="round"/></svg>

<div class="abs card" style="left:112px;top:1056px"><div class="ph" role="img" aria-label="Modern glass office building" style="background:linear-gradient(180deg,#2f6fc4,#cfd9e6 60%,#9aa3a8)"></div><h3>General Building</h3><p>Excepteur sint occaecat cupidatat non proident, sunt in culpa qui officia deserunt mollit anim id est laborum.</p><span class="btn">Read More</span></div>
<div class="abs card" style="left:450px;top:1056px"><div class="ph" role="img" aria-label="Electrician testing a panel with a meter" style="background:linear-gradient(90deg,#e9e4dc,#c9a66b 50%,#5d6168)"></div><h3>Electric Maintenance</h3><p>Excepteur sint occaecat cupidatat non proident, sunt in culpa qui officia deserunt mollit anim id est laborum.</p><span class="btn">Read More</span></div>
<div class="abs card" style="left:787px;top:1056px"><div class="ph" role="img" aria-label="Elevator doors in a lobby" style="background:linear-gradient(90deg,#8a8580,#6b5444 50%,#a0938a)"></div><h3>Elevator</h3><p>Excepteur sint occaecat cupidatat non proident, sunt in culpa qui officia deserunt mollit anim id est laborum.</p><span class="btn">Read More</span></div>

<section class="abs testi"></section>
<h2 class="abs sec-title" style="top:1652px">Our Testimonials</h2>
<div class="abs av" role="img" aria-label="Client portrait" style="left:392px;top:1759px;background:linear-gradient(#c9b48a,#8a7450)"></div>
<div class="abs av" role="img" aria-label="Client portrait" style="left:473px;top:1759px;background:linear-gradient(#d8d4cf,#5a6b80)"></div>
<div class="abs av" role="img" aria-label="Client portrait" style="left:684px;top:1759px;background:linear-gradient(#d9dfe6,#7c8ea3)"></div>
<div class="abs av" role="img" aria-label="Client portrait" style="left:724px;top:1759px;background:linear-gradient(#eee,#c9b9ae)"></div>
<div class="abs av" role="img" aria-label="Featured client portrait" style="left:541px;top:1740px;width:118px;height:118px;background:linear-gradient(#c89a78,#2f5a45)"></div>
<svg class="abs arrow" style="left:98px;top:1863px" viewBox="0 0 28 28"><circle cx="14" cy="14" r="14" fill="#0aa5e8"/><path d="M20 14H9M13 9l-5 5 5 5" stroke="#fff" stroke-width="3" fill="none" stroke-linecap="round" stroke-linejoin="round"/></svg>
<svg class="abs arrow" style="left:1074px;top:1863px" viewBox="0 0 28 28"><circle cx="14" cy="14" r="14" fill="#0aa5e8"/><path d="M8 14h11M15 9l5 5-5 5" stroke="#fff" stroke-width="3" fill="none" stroke-linecap="round" stroke-linejoin="round"/></svg>
<div class="abs tname">Lorem Ipsum</div>
<div class="abs trole">Customer</div>
<p class="abs tquote">Sed ut perspiciatis unde omnis iste natus error sit voluptatem accusantium doloremque laudantium, totam rem aperiam, eaque ipsa quae ab illo inventore veritatis et quasi architecto beatae vitae dicta sunt explicabo. Nemo enim ipsam voluptatem quia voluptas sit aspernatur aut odit aut fugit, sed quia consequuntur magni dolores eos qui ratione voluptatem sequi nesciunt.</p>
<div class="abs stars">☆☆☆☆☆</div>

<h2 class="abs sec-title" style="top:2256px">Our Portfolio</h2>
<svg class="abs arrow" style="left:61px;top:2467px" viewBox="0 0 28 28"><circle cx="14" cy="14" r="14" fill="#0aa5e8"/><path d="M20 14H9M13 9l-5 5 5 5" stroke="#fff" stroke-width="3" fill="none" stroke-linecap="round" stroke-linejoin="round"/></svg>
<svg class="abs arrow" style="left:1109px;top:2467px" viewBox="0 0 28 28"><circle cx="14" cy="14" r="14" fill="#0aa5e8"/><path d="M8 14h11M15 9l5 5-5 5" stroke="#fff" stroke-width="3" fill="none" stroke-linecap="round" stroke-linejoin="round"/></svg>

<div class="abs card" style="left:112px;top:2348px"><div class="ph" role="img" aria-label="Team meeting around a table with documents" style="background:linear-gradient(180deg,#e6eaee,#b9c3cc 60%,#6f6458)"></div><h3 style="font-weight:700">Job Order Contract (JOC) 2016-2023 | County of Marlow Bay</h3><p>Marlow Bay, CA | Task Orders Awarded: 155 Total Awarded Value: $20,000,000+</p><span class="btn">Read More</span></div>
<div class="abs card" style="left:449px;top:2348px"><div class="ph" role="img" aria-label="Hard hat resting on construction blueprints" style="background:linear-gradient(160deg,#f0f2f5,#dde3ea 55%,#8fa2b8)"></div><h3 style="font-weight:700">IDIQ/JOC 3-year Contract | Western Naval Works Dept.</h3><p>NAS Sable Flats, NV | Task Orders Awarded: 5 Total Awarded Value: $3,124,332</p><span class="btn">Read More</span></div>
<div class="abs card" style="left:786px;top:2348px"><div class="ph" role="img" aria-label="Two workers reviewing plans in a room under renovation" style="background:linear-gradient(180deg,#d8cfc4,#b6a592 60%,#8d8a86)"></div><h3 style="font-weight:700">Building Renovation, B. 6408 | Coastal State Guard Dept.</h3><p>Camp Harlan, CA Value: $1,001,747</p><span class="btn" style="margin-top:44px">Read More</span></div>

<h2 class="abs sec-title" style="top:2920px">Experience</h2>
<p class="abs exp-text">With vast experience in the trades, site superintendence, safety, quality control, and all aspects of general contracting, R W Builders can plan, manage and execute building construction projects in all sizes under any delivery method: design-build, CM at Risk, or design-bid-build.</p>

<div class="abs feat" style="left:101px"><svg viewBox="0 0 90 72" width="90"><circle cx="45" cy="28" r="10" fill="#0aa5e8"/><circle cx="20" cy="30" r="8" fill="#0aa5e8"/><circle cx="70" cy="30" r="8" fill="#0aa5e8"/><path d="M28 60c0-12 8-18 17-18s17 6 17 18z" fill="#0aa5e8"/><path d="M6 58c0-10 6-15 14-15 5 0 8 2 10 5-3 3-4 7-4 10z" fill="#0aa5e8"/><path d="M84 58c0-10-6-15-14-15-5 0-8 2-10 5 3 3 4 7 4 10z" fill="#0aa5e8"/></svg>Quickly mobilize<br>assets + personnel</div>
<div class="abs feat" style="left:299px"><svg viewBox="0 0 72 72" width="72"><path d="M14 26a14 14 0 0 1 28 0z" fill="#0aa5e8"/><rect x="10" y="26" width="36" height="4" fill="#0aa5e8"/><path d="M12 70c0-16 8-24 16-24s16 8 16 24z" fill="#0aa5e8"/><path d="M50 4l14 5v10c0 9-6 14-14 17-8-3-14-8-14-17V9z" fill="#0aa5e8"/><path d="M44 19l5 5 8-9" stroke="#fff" stroke-width="3" fill="none"/></svg>Commitment to<br>quality + safety</div>
<div class="abs feat" style="left:503px"><svg viewBox="0 0 72 72" width="72"><rect x="6" y="2" width="40" height="64" rx="5" fill="#0aa5e8"/><rect x="12" y="8" width="28" height="12" fill="#fff"/><g fill="#fff"><rect x="12" y="26" width="7" height="7"/><rect x="23" y="26" width="7" height="7"/><rect x="12" y="38" width="7" height="7"/><rect x="23" y="38" width="7" height="7"/><rect x="12" y="50" width="7" height="7"/><rect x="23" y="50" width="7" height="7"/></g><ellipse cx="58" cy="50" rx="12" ry="5" fill="#0aa5e8" stroke="#fff" stroke-width="2"/><ellipse cx="58" cy="58" rx="12" ry="5" fill="#0aa5e8" stroke="#fff" stroke-width="2"/><ellipse cx="58" cy="66" rx="12" ry="5" fill="#0aa5e8" stroke="#fff" stroke-width="2"/></svg>Complete projects<br>on time + on budget</div>
<div class="abs feat" style="left:706px"><svg viewBox="0 0 72 72" width="72"><path d="M36 6l8 6 10-1 3 10 9 5-4 9 4 9-9 5-3 10-10-1-8 6-8-6-10 1-3-10-9-5 4-9-4-9 9-5 3-10 10 1z" fill="#0aa5e8"/><circle cx="36" cy="36" r="16" fill="none" stroke="#fff" stroke-width="3"/><path d="M28 36l6 6 11-12" stroke="#fff" stroke-width="4" fill="none"/></svg>Qualified field +<br>office staff</div>
<div class="abs feat" style="left:901px"><svg viewBox="0 0 72 72" width="72"><path d="M22 18a14 14 0 0 1 28 0z" fill="#0aa5e8"/><rect x="18" y="18" width="36" height="4" fill="#0aa5e8"/><circle cx="36" cy="30" r="9" fill="#0aa5e8"/><path d="M16 66c0-16 9-24 20-24s20 8 20 24z" fill="#0aa5e8"/><circle cx="40" cy="56" r="9" fill="#fff"/><circle cx="40" cy="56" r="5" fill="#0aa5e8"/></svg>Value engineering</div>

<footer class="abs footer" role="img" aria-label="Dark faded excavator backdrop"></footer>
<div class="abs flogo">R W Builders</div>
<div class="abs fcontacts">
  <div class="contact" style="width:162px"><span class="ic blue"><svg width="16" height="16" viewBox="0 0 24 24"><path fill="#fff" d="M6.6 10.8a15 15 0 0 0 6.6 6.6l2.2-2.2c.3-.3.7-.4 1-.2 1.1.4 2.3.6 3.6.6.6 0 1 .4 1 1V20c0 .6-.4 1-1 1A17 17 0 0 1 3 4c0-.6.4-1 1-1h3.5c.6 0 1 .4 1 1 0 1.3.2 2.5.6 3.6.1.3 0 .7-.2 1z"/></svg></span><span><b>Call</b>(555) 410-2286</span></div>
  <div class="contact" style="width:205px"><span class="ic blue"><svg width="16" height="16" viewBox="0 0 24 24"><rect x="2" y="5" width="20" height="14" rx="2" fill="#fff"/><path d="M2 6l10 7 10-7" stroke="#0aa5e8" stroke-width="2" fill="none"/></svg></span><span><b>Email</b>hello@rwbuilders.biz</span></div>
  <div class="contact"><span class="ic blue"><svg width="16" height="16" viewBox="0 0 24 24"><path fill="#fff" d="M12 2a7 7 0 0 0-7 7c0 5 7 13 7 13s7-8 7-13a7 7 0 0 0-7-7zm0 9.5A2.5 2.5 0 1 1 12 6.5a2.5 2.5 0 0 1 0 5z"/></svg></span><span><b>Location</b>P.O. Box 2480 Arroyo Vista, CA 93401</span></div>
</div>
<div class="abs copy">Copyright © 2024 R W Builders - All Rights Reserved.</div>

</body>
</html>
```